House flipping business web site needed

pinecrestholdingsgroup.example.
I am a residential developer in Northern NJ and I am looking for a fresh new updated website. I have an intro video about my company being made now. I don't update it very often but I want an easy format that I can add update photos to on projects I have worked on or homes I renovate for sale.

Target Market(s)

investors into my projects so a portfolio , people looking to sell their homes to me.

Industry/Entity Type

Real Estate Development

Number of Pages Required

4 page

Font styles to use
Serif

Colors
33b8a4
39a9d7
cadf82

Requirements
Must have
• space for an intro video about my company
• a portfolio with pictures and information about each project
• Markets we serve- Morris County, NJ
• My logo- already created
• SEO
• Yes I would like this to function over all platforms. Phone, computer, all platforms.
• history and background page
• I am looking for a completed page that I can upload to the site that hosts my website
Nice to have
• I want something creative, easy to navigate. modern.

```html
<!DOCTYPE html>
<html lang="en">
<head>
<meta charset="utf-8">
<title>Pinecrest Holdings — Investing in our neighborhoods</title>
<link href="https://fonts.googleapis.com/css2?family=Noto+Serif:wght@400;700&family=Open+Sans:wght@400;600;700&display=swap" rel="stylesheet">
<style>
:root{
  --teal:#33b8a4;
  --blue:#39a9d7;
  --lime:#cadf82;
  --ink:#222;
  --text:#333;
  --muted:#8a8f96;
  --header-bg:#f7f7f9;
  --contact-bg:#ececec;
  --form-bg:#1b1b21;
  --field-line:#3a3a44;
  --white:#fff;
}
*{box-sizing:border-box;margin:0;padding:0}
html,body{width:1200px;height:3273px;overflow:hidden}
body{position:relative;background:var(--white);font-family:"Open Sans",Arial,sans-serif;color:var(--text)}
.abs{position:absolute}
.serif{font-family:"Noto Serif",Georgia,serif}

/* Header */
.site-header{left:0;top:0;width:1200px;height:115px;background:var(--header-bg)}
.brand{left:176px;top:36px;display:flex;align-items:center;gap:10px;font-family:"Noto Serif",Georgia,serif;font-weight:700;font-size:17px;letter-spacing:1px;color:var(--teal)}
.brand-dot{width:22px;height:22px;border-radius:50%;background:var(--teal)}
.main-nav{left:720px;top:58px;display:flex;gap:30px;font-family:"Noto Serif",Georgia,serif;font-size:13px;color:var(--ink)}
.main-nav .active{color:var(--blue);position:relative}
.main-nav .active::after{content:"";position:absolute;left:-12px;right:-12px;top:53px;height:2px;background:var(--blue)}

/* Hero */
.hero{left:0;top:115px;width:1200px;height:545px}
.hero-title{left:340px;top:395px;width:520px;height:60px;background:var(--blue);color:var(--white);font-family:"Noto Serif",Georgia,serif;font-size:42px;line-height:60px;text-align:center}
.hero-sub{left:335px;top:460px;width:530px;height:32px;background:var(--teal);color:var(--white);font-size:19px;letter-spacing:4px;line-height:32px;text-align:center}
.slider-dots{left:558px;top:612px;display:flex;gap:10px}
.slider-dots span{width:10px;height:10px;border-radius:50%;background:var(--white)}

/* About */
.section-title{left:0;width:1200px;text-align:center;font-family:"Noto Serif",Georgia,serif;letter-spacing:5px}
.about-title{top:690px;font-size:34px;color:var(--teal)}
.title-rule{left:390px;width:420px;height:1px;background:#c9c9c9}
.video{left:190px;top:770px;width:400px;height:295px}
.about-copy{left:617px;top:780px;width:395px;font-size:11.5px;line-height:19px;color:var(--ink)}
.about-copy p{margin-bottom:4px}
.about-copy h3{font-weight:400;font-size:24px;color:var(--blue);margin:10px 0 6px}
.btn-more{display:inline-block;margin-top:14px;background:var(--teal);color:var(--white);font-size:10px;font-weight:700;padding:10px 14px}

/* Portfolio */
.portfolio-band{left:0;top:1125px;width:1200px;height:1030px}
.portfolio-title{top:1185px;font-size:34px;color:var(--white)}
.filters{left:0;top:1278px;width:1200px;display:flex;justify-content:center;gap:22px;font-size:10px;letter-spacing:1px;color:#e6f3fa}
.filters .active{color:var(--lime);padding:0 12px 8px;border-bottom:2px solid var(--lime)}
.filter-rule{left:410px;top:1303px;width:380px;height:1px;background:rgba(255,255,255,.35)}
.grid{left:161px;top:1327px;width:878px;display:grid;grid-template-columns:repeat(4,202px);grid-template-rows:repeat(3,223px);gap:24px 23px}
.tile{position:relative}
.t-wide{grid-column:span 2}
.t-tall{grid-row:span 2}
.tile-card{position:absolute;inset:0;background:rgba(51,184,164,.82);color:var(--white);padding:96px 26px 0}
.tile-card .icons{position:absolute;left:26px;top:66px;display:flex;gap:10px}
.tile-card .icons span{width:22px;height:22px;border:1px solid var(--white);background:rgba(255,255,255,.2)}
.tile-card h4{font-weight:400;font-size:16px}
.tile-card p{font-size:9px;margin-top:4px}

/* Contact */
.contact-bg{left:0;top:2100px;width:1200px;height:620px;background:var(--contact-bg)}
.kicker{left:0;top:2207px;width:1200px;text-align:center;font-size:10px;letter-spacing:1px;color:var(--blue)}
.contact-title{left:0;top:2228px;width:1200px;text-align:center;font-family:"Noto Serif",Georgia,serif;font-size:28px;color:var(--ink)}
.info{top:2332px;width:260px;text-align:center;font-size:13px;line-height:21px;color:var(--muted)}
.info svg{display:block;margin:0 auto 18px}
.contact-form{left:290px;top:2483px;width:578px;height:270px;background:var(--form-bg);z-index:2}
.field{position:absolute;border:1px solid var(--field-line);color:#666;font-size:8px;letter-spacing:1px;padding:10px 12px}
.send{position:absolute;left:395px;top:202px;width:118px;height:34px;background:var(--blue);color:var(--white);font-size:9px;font-weight:700;letter-spacing:.5px;text-align:center;line-height:34px}
.map{left:0;top:2705px;width:1200px;height:345px}

/* Footer */
.footer-nav{left:0;top:3084px;width:1200px;display:flex;justify-content:center;gap:30px;font-family:"Noto Serif",Georgia,serif;font-size:13px;color:var(--ink)}
.footer-nav .active{color:var(--blue)}
.social{left:526px;top:3127px;display:flex;gap:44px}
.social span{width:18px;height:18px;border-radius:50%;background:#9aa0a6}
.social .accent{background:var(--blue)}
.footer-brand{left:0;top:3170px;width:1200px;text-align:center;font-family:"Noto Serif",Georgia,serif;font-weight:700;font-size:15px;letter-spacing:1px;color:var(--teal)}
.copyright{left:0;top:3230px;width:1200px;text-align:center;font-size:10px;letter-spacing:1px;color:var(--muted)}
</style>
</head>
<body>

<header class="site-header abs">
  <div class="brand abs"><span class="brand-dot"></span>PINECREST HOLDINGS</div>
  <nav class="main-nav abs">
    <span class="active">Home</span><span>About Us</span><span>Portfolio</span><span>Contact Us</span>
  </nav>
</header>

<svg class="hero abs" viewBox="0 0 1200 545" role="img" aria-label="Photo of a renovated two-storey house with stone retaining wall and bare trees">
  <defs>
    <linearGradient id="heroFill" x1="0" y1="0" x2="0" y2="1">
      <stop offset="0" stop-color="#b9b6b0"/>
      <stop offset=".55" stop-color="#8d8476"/>
      <stop offset="1" stop-color="#5d554b"/>
    </linearGradient>
  </defs>
  <polygon points="0,0 1200,0 1200,475 600,545 0,475" fill="url(#heroFill)"/>
</svg>
<div class="hero-title abs">Pinecrest Holdings</div>
<div class="hero-sub abs">INVESTING IN OUR NEIGHBORHOODS</div>
<div class="slider-dots abs"><span></span><span></span><span></span><span></span></div>

<h2 class="section-title about-title abs">About My Company</h2>
<div class="title-rule abs" style="top:745px"></div>

<svg class="video abs" viewBox="0 0 400 295" role="img" aria-label="Intro video still of a house exterior">
  <defs>
    <linearGradient id="videoFill" x1="0" y1="0" x2="0" y2="1">
      <stop offset="0" stop-color="#5a5a58"/>
      <stop offset="1" stop-color="#23241f"/>
    </linearGradient>
  </defs>
  <rect width="400" height="295" fill="url(#videoFill)"/>
  <circle cx="200" cy="130" r="28" fill="rgba(0,0,0,.25)" stroke="#fff" stroke-width="2"/>
  <polygon points="192,116 192,144 214,130" fill="#fff"/>
</svg>

<div class="about-copy abs">
  <p>We only buy and renovate homes in our neighborhoods right here in the Morris County, NJ area.</p>
  <p>Is a house in your neighborhood an eyesore? Is it vacant, boarded up and a hazard to the neighborhood? Please contact us and we can help transform that property into a beautiful home.</p>
  <h3 class="serif">How we can help</h3>
  <p>Do you need to sell your home fast to avoid foreclosure, have estate home you do not want to fix to put on the market, moving for a job and need your house sold fast. We can help. Contact us now.</p>
  <span class="btn-more">LEARN MORE</span>
</div>

<svg class="portfolio-band abs" viewBox="0 0 1200 1030" aria-hidden="true">
  <polygon points="0,85 600,0 1200,85 1200,960 600,1025 0,960" fill="var(--blue)"/>
</svg>
<h2 class="section-title portfolio-title abs">Portfolio</h2>
<div class="title-rule abs" style="top:1240px;left:495px;width:210px;background:rgba(255,255,255,.6)"></div>
<div class="filter-rule abs"></div>
<div class="filters abs"><span class="active">SHOW ALL</span><span>PHOTOGRAPHY</span><span>BRANDING</span><span>GRAPHIC DESIGN</span></div>

<div class="grid abs">
  <div class="tile t-wide" role="img" aria-label="Renovated house with new deck" style="background:linear-gradient(#9a958b,#5f5a4e)"></div>
  <div class="tile" role="img" aria-label="Newly furnished house in Rockaway, NJ" style="background:linear-gradient(#b8b2a8,#6f7a5e)">
    <div class="tile-card"><div class="icons"><span></span><span></span></div><h4 class="serif">Rockaway, NJ</h4><p>Newly Furnished</p></div>
  </div>
  <div class="tile" role="img" aria-label="Green-sided house exterior" style="background:linear-gradient(#c3c8c6,#3f5a4f)"></div>
  <div class="tile" role="img" aria-label="Framed interior under renovation" style="background:linear-gradient(#a47f55,#c9b58e)"></div>
  <div class="tile t-tall" role="img" aria-label="Stone wall entrance with new paver walkway" style="background:linear-gradient(#7a6e62,#9c9181 60%,#b8a77a)"></div>
  <div class="tile t-wide" role="img" aria-label="Staged bedroom with dark bed set" style="background:linear-gradient(#b1a593,#3b3734)"></div>
  <div class="tile" role="img" aria-label="Renovated kitchen with white cabinets" style="background:linear-gradient(#d9d7d2,#5b5854)"></div>
  <div class="tile" role="img" aria-label="Living room with dark sofa" style="background:linear-gradient(#c7bfb2,#2e2b29)"></div>
  <div class="tile" role="img" aria-label="Porch under construction" style="background:linear-gradient(#b8bcc0,#8a5a3c)"></div>
</div>

<div class="contact-bg abs"></div>
<div class="kicker abs">STAY IN TOUCH</div>
<h2 class="contact-title abs">Contact us</h2>
<div class="title-rule abs" style="top:2270px;left:530px;width:140px"></div>

<div class="info abs" style="left:148px">
  <svg width="14" height="24" viewBox="0 0 14 24" aria-hidden="true"><rect x="1" y="1" width="12" height="22" rx="2" fill="none" stroke="var(--blue)" stroke-width="1.6"/><circle cx="7" cy="19" r="1.2" fill="var(--blue)"/></svg>
  Phone: (555) 010-5678<br>Fax: (555) 010-8290
</div>
<div class="info abs" style="left:448px">
  <svg width="18" height="24" viewBox="0 0 18 24" aria-hidden="true"><path d="M9 1C4.6 1 1.5 4.3 1.5 8.5 1.5 14 9 23 9 23s7.5-9 7.5-14.5C16.5 4.3 13.4 1 9 1z" fill="none" stroke="var(--blue)" stroke-width="1.6"/><circle cx="9" cy="8.5" r="2.6" fill="none" stroke="var(--blue)" stroke-width="1.6"/></svg>
  Pinecrest Holdings Group<br>Morris County, NJ<br>862-555-0142
</div>
<div class="info abs" style="left:748px">
  <svg width="24" height="24" viewBox="0 0 24 24" aria-hidden="true"><rect x="1" y="5" width="22" height="14" fill="none" stroke="var(--blue)" stroke-width="1.6"/><path d="M1 5l11 8 11-8" fill="none" stroke="var(--blue)" stroke-width="1.6"/></svg>
  hello@pinecrestholdingsgroup.example
</div>

<div class="map abs" role="img" aria-label="Street map showing the office location beside the waterfront" style="background:linear-gradient(90deg,#e6e2d8 0%,#ddd8cc 52%,#9fc2f3 56%,#a4c6f5 100%)"></div>

<form class="contact-form abs">
  <div class="field" style="left:50px;top:45px;width:226px;height:37px">NAME *</div>
  <div class="field" style="left:50px;top:97px;width:226px;height:37px">EMAIL *</div>
  <div class="field" style="left:50px;top:149px;width:226px;height:37px">SUBJECT *</div>
  <div class="field" style="left:288px;top:45px;width:225px;height:141px">MESSAGE *</div>
  <div class="send">SEND MESSAGE</div>
</form>

<nav class="footer-nav abs"><span class="active">Home</span><span>About Us</span><span>Portfolio</span><span>Contact Us</span></nav>
<div class="social abs"><span></span><span class="accent"></span><span></span></div>
<div class="footer-brand abs">PINECREST HOLDINGS</div>
<div class="copyright abs">Copyright©2016 . www.pinecrestholdingsgroup.example</div>

</body>
</html>
```